International Clinical Software Company needs a new business card design

We are looking for a new business card design for our company that has recently expanded into the UK market, making us a multinational company.
After having rebranded our website and produced a new style guide, we are looking for a business card that is creative and attention grabbing, while being consistent with the style and colour scheme used on the new website, www.plumvora.example
We produce care management technology for the aged care market, but the main aspect we aim to communicate is the human element of our software, and the way it assists in providing better care for aged people, and stronger relationships between aged people and the staff that care for them.
Our current business card is a dark green with gold text, which makes the text quite difficult to read, not very aesthetically appealing and the colour scheme looks quite dated.
We would like something fresh and modern, that can still be colourful but doesn't use large blocks of dark colour, and uses the colours within our logo.
Something tying in with the leaves that are used in our logo could work quite nicely, along with the Autumn/Fall colours of soft greens, yellows and reds (also in our existing logo). However also happy to look at fresh, completely out of the box ideas we may not have yet considered.
Target Market(s)
The people that receive this business card work in the aged card or health industry and are either corporate/management level staff or clinical (Registered Nurses, care workers etc.)
Industry/Entity Type
Health Product
Contact Information for Business Card
Company Name - BrindlewayCare
Company locations: United Kingdom, Australia, New Zealand
Staff Details:
Staff name: Derek Mallow
Staff job title: Executive Chairman
Staff email: d.mallow@plumvora.example
Office phone number: 01742 918576
Font styles to use
Other font styles liked:
- Calibri
Requirements
Must have
- Must include the BrindlewayCare brand name in it's current font
- Must include logo (3 leaves in gold circle)
- Must include Business Card Details
Nice to have
- Elements of gold
- White space
- Something autumn themed but not too cliched
Should not have
- No blue - used by a major competitor and we would like to differentiate from them
- Large blocks of dark green colour (the green that appears in our leaves on the logo on our current business card is the background colour and it is far too dark)

```html
<!DOCTYPE html>
<html lang="en">
<head>
<meta charset="utf-8">
<title>BrindlewayCare — Business Card</title>
<link rel="stylesheet" href="https://fonts.googleapis.com/css2?family=Carlito:wght@400;700&display=swap">
<style>
  :root {
    --page-bg: #ebe7e2;
    --card-gold-light: #d8c6a4;
    --card-gold-dark: #b49a70;
    --accent-red: #8c1d38;
    --accent-red-dark: #6e1229;
    --name-red: #8b1a2e;
    --ring-gold: #b5955e;
    --frost: rgba(244, 238, 228, 0.55);
    --wordmark-brown: #5a4226;
    --text-light: #ffffff;
  }
  * { margin: 0; padding: 0; box-sizing: border-box; }
  html, body {
    width: 1200px;
    height: 969px;
    overflow: hidden;
    background: var(--page-bg);
    font-family: "Carlito", Calibri, sans-serif;
  }
  .business-card {
    position: absolute;
    left: 120px;
    top: 212px;
    width: 960px;
    height: 546px;
    border-radius: 30px;
    overflow: hidden;
    background: linear-gradient(160deg, var(--card-gold-light) 0%, var(--card-gold-dark) 100%);
    box-shadow: 0 0 0 2px rgba(255,255,255,0.5) inset;
  }
  .accent-band {
    position: absolute;
    top: 0;
    right: 0;
    width: 240px;
    height: 100%;
    background: linear-gradient(180deg, var(--accent-red) 0%, var(--accent-red-dark) 100%);
  }
  .brand-ring {
    position: absolute;
    left: 0;
    top: 0;
  }
  .brand-lockup {
    position: absolute;
    left: 405px;
    top: 140px;
    width: 530px;
    text-align: center;
  }
  .brand-dot {
    display: block;
    width: 96px;
    height: 96px;
    margin: 0 auto 22px;
    border-radius: 50%;
    border: 4px solid var(--ring-gold);
  }
  .brand-name {
    font-size: 64px;
    font-weight: 400;
    color: var(--wordmark-brown);
    letter-spacing: 1px;
    line-height: 1;
  }
  .contact-block {
    position: absolute;
    left: 66px;
    top: 112px;
    color: var(--text-light);
  }
  .person-name {
    font-size: 32px;
    font-weight: 700;
    color: var(--name-red);
    letter-spacing: 0.5px;
    line-height: 1.1;
    text-transform: uppercase;
  }
  .person-title {
    font-size: 25px;
    line-height: 1.3;
  }
  .locations {
    list-style: none;
    margin-top: 30px;
    font-size: 25px;
    line-height: 35px;
  }
  .contact-list {
    list-style: none;
    margin-top: 18px;
    font-size: 25px;
    line-height: 37px;
  }
  .contact-list li {
    display: flex;
    align-items: center;
    gap: 14px;
  }
  .contact-icon {
    width: 20px;
    height: 20px;
    flex: none;
    fill: var(--name-red);
  }
</style>
</head>
<body>
  <div class="business-card">
    <div class="accent-band"></div>

    <svg class="brand-ring" width="960" height="546" viewBox="0 0 960 546" aria-hidden="true">
      <circle cx="670" cy="273" r="262" fill="var(--frost)" stroke="var(--ring-gold)" stroke-width="4"/>
      <circle cx="670" cy="273" r="252" fill="none" stroke="rgba(255,255,255,0.6)" stroke-width="2"/>
    </svg>

    <div class="brand-lockup">
      <span class="brand-dot"></span>
      <div class="brand-name">BrindlewayCare</div>
    </div>

    <div class="contact-block">
      <h1 class="person-name">Derek Mallow</h1>
      <p class="person-title">Executive Chairman</p>
      <ul class="locations">
        <li>United Kingdom</li>
        <li>Australia</li>
        <li>New Zealand</li>
      </ul>
      <ul class="contact-list">
        <li>
          <svg class="contact-icon" viewBox="0 0 20 20" aria-hidden="true"><path d="M4 1.5l3 0.5 1.5 4-2 1.6a11 11 0 0 0 5.9 5.9L14 11.5l4 1.5 0.5 3c0 1.5-1.3 2.5-2.8 2.5C8 18.5 1.5 12 1.5 4.3 1.5 2.8 2.5 1.5 4 1.5z"/></svg>
          <span>01742 918576</span>
        </li>
        <li>
          <svg class="contact-icon" viewBox="0 0 20 20" aria-hidden="true"><path d="M1 4h18v1.2L10 11 1 5.2z"/><path d="M1 7.2l9 5.8 9-5.8V16H1z"/></svg>
          <span>d.mallow@plumvora.example</span>
        </li>
        <li>
          <svg class="contact-icon" viewBox="0 0 20 20" aria-hidden="true"><circle cx="10" cy="10" r="9"/><path d="M10 1.5c-2.5 2.5-3.5 5.5-3.5 8.5s1 6 3.5 8.5M10 1.5c2.5 2.5 3.5 5.5 3.5 8.5s-1 6-3.5 8.5M1.5 10h17" stroke="var(--card-gold-light)" stroke-width="1.2" fill="none"/></svg>
          <span>www.plumvora.example</span>
        </li>
      </ul>
    </div>
  </div>
</body>
</html>
```